SnackOrbit!!! A Vending Machine Business Looking for an attractive website.

We are a vending machine business in Northern Michigan. We have changed our name and have rebranded our company. We would like an attractive website that shares who we are, what services we provide, the products we offer in our machines, along with a form businesses can fill out to see if they are a good fit for our company. I would like to have a Home Page, About SnackOrbit, Why Choose SnackOrbit?, Products & Services, Contact Us (With a Login Option), and a page with a questionnaire for thos interested in getting a FREE Vending Machine.

Target Market(s)

Businesses, Campgrounds, Schools, and many more in Northern Michigan

Industry/Entity Type

Vending Machines

Coding

Coded - Design and coding required

Number of Pages Required

5+ page

Requirements
Must have
• An inviting and enticing Home Page. I want to get my potential clients engaged in our website.
Nice to have
• Possibly background photos from Northern Michigan
Should not have
• A corporate feel. I do not want a boring website.

```html
<!DOCTYPE html>
<html lang="en">
<head>
<meta charset="utf-8">
<title>SnackOrbit – Crave. Vend. Repeat.</title>
<link href="https://fonts.googleapis.com/css2?family=Lexend:wght@400;500;600;700;800&display=swap" rel="stylesheet">
<style>
:root{
  --navy:#27224f;
  --navy-dark:#1f1a45;
  --green:#2f5321;
  --ink:#1c1c24;
  --muted:#4a4a55;
  --line:#e4e4ea;
  --gold:#f5b301;
  --white:#ffffff;
}
*{box-sizing:border-box;margin:0;padding:0}
html,body{width:1200px;height:3288px;overflow:hidden}
body{font-family:"Lexend",sans-serif;color:var(--ink);background:var(--white);position:relative}
a{color:inherit;text-decoration:none}

.site-header{height:84px;display:flex;align-items:center;padding:0 106px;justify-content:space-between}
.brand{display:flex;align-items:center;gap:10px;font-size:30px;font-weight:700;color:var(--navy)}
.brand-dot{width:26px;height:26px;border-radius:50%;background:var(--green)}
.main-nav{display:flex;align-items:center;gap:32px;font-size:13px;color:var(--ink)}
.main-nav .btns{display:flex;gap:8px}
.pill{display:inline-block;padding:10px 20px;border-radius:20px;color:var(--white);font-size:13px}
.pill.green{background:var(--green)}
.pill.navy{background:var(--navy)}

.hero{position:relative;height:544px;overflow:hidden}
.hero-photo{position:absolute;inset:0;background:linear-gradient(90deg,#0d0c10 0%,#1a1620 38%,#6a2a5c 60%,#b83a7a 75%,#8a1e28 100%)}
.hero-copy{position:relative;padding:150px 106px 0;color:var(--white)}
.hero-copy h1{font-size:47px;font-weight:800;line-height:1.14}
.hero-copy p{font-size:18px;margin:22px 0 26px}
.btn-green{display:inline-block;background:var(--green);color:var(--white);padding:12px 24px;border-radius:22px;font-size:14px}

.about{background:var(--navy);height:338px;text-align:center;color:var(--white);padding-top:64px}
.about h2{font-size:31px;font-weight:600;margin-bottom:12px}
.about p{width:740px;margin:0 auto;font-size:13px;line-height:22px}
.btn-outline{display:inline-block;margin-top:22px;border:1px solid var(--white);padding:8px 16px;border-radius:3px;font-size:13px}

.why{height:819px;position:relative}
.why h2{text-align:center;font-size:31px;font-weight:600;padding-top:78px}
.feature{position:absolute;width:442px;height:232px;border:1px solid var(--line);padding:58px 14px 0}
.feature-icon{position:absolute;top:-38px;left:14px;width:77px;height:77px;border-radius:50%;background:var(--navy);border:3px solid var(--white);box-shadow:0 0 0 2px var(--navy);display:flex;align-items:center;justify-content:center}
.feature h3{font-size:15px;font-weight:500;margin-bottom:8px}
.feature p{font-size:13px;line-height:21.7px;color:var(--muted)}
.feature b{color:var(--ink);font-weight:500}

.cta{position:relative;height:527px;overflow:hidden}
.cta-photo{position:absolute;inset:0;background:linear-gradient(90deg,#7f8c95 0%,#8b98a1 40%,#6d7c86 100%)}
.machines{position:absolute;left:30px;top:58px;width:548px;height:450px;background:linear-gradient(90deg,#2a2c30 0 45%,#c9221a 50% 100%);border-radius:4px}
.cta-copy{position:absolute;left:677px;top:155px;width:390px;color:var(--white)}
.cta-copy h2{font-size:31px;font-weight:500;line-height:39px}
.cta-copy p{font-size:13px;line-height:21.7px;margin:14px 0 20px}
.btn-navy{display:inline-block;background:var(--navy);padding:9px 16px;border-radius:3px;font-size:13px}

.testimonials{height:599px;position:relative}
.testimonials h2{text-align:center;font-size:31px;font-weight:600;padding-top:76px}
.review{position:absolute;width:268px;border:1px solid var(--line);text-align:center;padding:22px 14px 0;height:282px;background:var(--white)}
.quote{position:absolute;left:14px;top:-32px;font-size:60px;font-weight:800;color:var(--navy);line-height:1}
.avatar{width:44px;height:44px;border-radius:50%;background:linear-gradient(#d9c9bd,#b08b72);margin:0 auto 10px}
.stars{color:var(--gold);font-size:13px;letter-spacing:5px;margin-bottom:18px}
.review p{font-size:13.5px;line-height:23px;color:var(--muted)}
.review .name{margin-top:34px;font-size:12px;font-weight:600;color:var(--ink)}
.arrow{position:absolute;top:2577px;width:34px;height:34px;border-radius:50%;background:var(--white);box-shadow:0 1px 6px rgba(0,0,0,.15);display:flex;align-items:center;justify-content:center}

.site-footer{position:absolute;top:2911px;left:0;width:1200px;height:377px;background:var(--navy);color:var(--white)}
.footer-badge{position:absolute;top:2831px;left:487px;width:227px;height:227px;border-radius:50%;background:var(--white);border:8px solid var(--green);display:flex;align-items:center;justify-content:center;font-size:30px;font-weight:700;color:var(--navy);z-index:2}
.footer-nav{position:absolute;top:168px;left:140px;width:920px;height:57px;border-top:1px solid rgba(255,255,255,.3);border-bottom:1px solid rgba(255,255,255,.3);display:flex;justify-content:space-around;align-items:center;font-size:13px}
.footer-nav .current{font-weight:600}
.contacts{position:absolute;top:262px;left:200px;width:820px;display:flex;justify-content:space-between}
.contact{display:flex;align-items:center;gap:14px;font-size:13px;line-height:18px}
.contact .ic{width:40px;height:40px;border-radius:50%;background:rgba(255,255,255,.15);display:flex;align-items:center;justify-content:center}
.contact small{font-size:11px;font-weight:600;display:block}
.contact .big{font-size:15px}
.sep{width:1px;height:30px;background:rgba(255,255,255,.3);align-self:center}
.legal{position:absolute;top:348px;left:142px;font-size:13px}
.socials{position:absolute;top:339px;left:926px;display:flex;gap:6px}
.socials span{width:30px;height:30px;border:1px solid var(--white);border-radius:50%}
</style>
</head>
<body>

<header class="site-header">
  <a class="brand" href="#"><span class="brand-dot"></span>SnackOrbit</a>
  <nav class="main-nav">
    <a href="#">Home</a><a href="#">About SnackOrbit</a><a href="#">Why Choose Us?</a><a href="#">Products &amp; Services</a>
    <span class="btns"><a class="pill green" href="#">Contact Us</a><a class="pill navy" href="#">Login</a></span>
  </nav>
</header>

<section class="hero">
  <div class="hero-photo" role="img" aria-label="Night street scene with a person in a floral kimono beside a lit drinks vending machine"></div>
  <div class="hero-copy">
    <h1>SnackOrbit: Crave.<br>Vend. Repeat.</h1>
    <p>Elevating Snacking, One Vend at a Time</p>
    <a class="btn-green" href="#">Contact Us ➔</a>
  </div>
</section>

<section class="about">
  <h2>About SnackOrbit</h2>
  <p>Welcome to SnackOrbit, where snacking meets delight! We're not just about vending machines;we're your culinary companions, your flavor curators, and your secret stash of happiness. Marcus and Elena, the dynamic duo behind SnackOrbit, have a passion for all things tasty. With backgrounds in sales and a penchant for personal connections, they've transformed the vending experience into an art form.</p>
  <a class="btn-outline" href="#">Read More</a>
</section>

<section class="why">
  <h2>Why Choose SnackOrbit?</h2>
  <article class="feature" style="left:140px;top:197px">
    <div class="feature-icon"><svg width="36" height="36" viewBox="0 0 24 24" fill="none" stroke="#fff" stroke-width="1.5"><path d="M12 21s-7-6-7-11a7 7 0 0 1 14 0c0 5-7 11-7 11z"/><path d="M12 13l-3-3a2 2 0 0 1 3-2 2 2 0 0 1 3 2z"/></svg></div>
    <h3>Local Love</h3>
    <p>We celebrate the heart of Michigan by partnering with local legends. Say hello to <b>Pinecrest Jerky Co. and Northshore Kettle Chips</b>—our hometown heroes. Their flavors dance on your taste buds, and we're thrilled to bring them straight to your workplace.</p>
  </article>
  <article class="feature" style="left:618px;top:197px">
    <div class="feature-icon"><svg width="36" height="36" viewBox="0 0 24 24" fill="none" stroke="#fff" stroke-width="1.5"><circle cx="9" cy="9" r="5"/><circle cx="15" cy="15" r="5"/></svg></div>
    <h3>Unleash Your Cravings</h3>
    <p>SnackOrbit isn't bound by corporate ties. We're the rebels of the vending world. Craving a bag of crispy, kettle-cooked chips? Done. Hankering for jerky that packs a punch? We've got you covered. Our machines are like treasure chests, waiting for you to unlock flavor magic.</p>
  </article>
  <article class="feature" style="left:140px;top:501px">
    <div class="feature-icon"><svg width="36" height="36" viewBox="0 0 24 24" fill="none" stroke="#fff" stroke-width="1.5"><path d="M7 11v9H4v-9zM7 11l4-7a2 2 0 0 1 2 2v4h5a2 2 0 0 1 2 2l-2 7H7"/></svg></div>
    <h3>Quality Meets Convenience</h3>
    <p>Imagine this: You're mid-meeting, and your stomach growls. Fear not! SnackOrbit's machines offer top-notch snacks and beverages. It's like having a mini food festival at your fingertips. <b>Tap to Pay</b> : No fumbling for change! SnackOrbit accepts tap-to-pay options, credit cards, and even phone wallet pay. Seamless snacking, guaranteed.</p>
  </article>
  <article class="feature" style="left:618px;top:501px">
    <div class="feature-icon"><svg width="36" height="36" viewBox="0 0 24 24" fill="none" stroke="#fff" stroke-width="1.5"><path d="M4 20h16M6 20v-5M10 20v-8M14 20v-6M18 20v-11M5 12l5-4 4 3 6-6"/></svg></div>
    <h3>Pandemic-Proof &amp; Recession-Ready</h3>
    <p>Life throws curveballs, but SnackOrbit stands strong. Our vending machines are the unsung heroes of resilience. Rain or shine, they're there, serving up joy.</p>
  </article>
</section>

<section class="cta">
  <div class="cta-photo" role="img" aria-label="Grey wall backdrop"></div>
  <div class="machines" role="img" aria-label="A snack vending machine and a red drinks vending machine side by side"></div>
  <div class="cta-copy">
    <h2>Ready to experience the SnackOrbit difference?</h2>
    <p>Sign up now and let's connect. Taste the future of snacking firsthand! Contact us today and explore how our vending magic can elevate your space.</p>
    <a class="btn-navy" href="#">Contact Us</a>
  </div>
</section>

<section class="testimonials">
  <h2>Customer Testimonials</h2>
  <article class="review" style="left:140px;top:178px"><span class="quote">“</span><div class="avatar" role="img" aria-label="Customer portrait"></div><div class="stars">★★★★★</div><p>Lorem ipsum dolor sit amet, consectetur adipiscing elit, sed do eiusmod tempor incididunt ut labore et dolore magna aliqua.</p><div class="name">-Owen Hartley</div></article>
  <article class="review" style="left:466px;top:143px"><span class="quote">“</span><div class="avatar" role="img" aria-label="Customer portrait"></div><div class="stars">★★★★★</div><p>Lorem ipsum dolor sit amet, consectetur adipiscing elit, sed do eiusmod tempor incididunt ut labore et dolore magna aliqua.</p><div class="name">-Rachel Lindqvist</div></article>
  <article class="review" style="left:792px;top:178px"><span class="quote">“</span><div class="avatar" role="img" aria-label="Customer portrait"></div><div class="stars">★★★★★</div><p>Lorem ipsum dolor sit amet, consectetur adipiscing elit, sed do eiusmod tempor incididunt ut labore et dolore magna aliqua.</p><div class="name">-Daniel Brooks</div></article>
</section>
<span class="arrow" style="left:91px"><svg width="14" height="14" viewBox="0 0 14 14" fill="none" stroke="#999" stroke-width="1.4"><path d="M13 7H1M6 2L1 7l5 5"/></svg></span>
<span class="arrow" style="left:1074px"><svg width="14" height="14" viewBox="0 0 14 14" fill="none" stroke="#222" stroke-width="1.4"><path d="M1 7h12M8 2l5 5-5 5"/></svg></span>

<div class="footer-badge">SnackOrbit</div>
<footer class="site-footer">
  <nav class="footer-nav"><a class="current" href="#">Home</a><a href="#">About</a><a href="#">Why Choose Us</a><a href="#">Products &amp; Services</a><a href="#">Contact Us</a></nav>
  <div class="contacts">
    <div class="contact"><span class="ic"><svg width="18" height="18" viewBox="0 0 24 24" fill="none" stroke="#fff" stroke-width="1.6"><rect x="3" y="6" width="18" height="12"/><path d="M3 6l9 7 9-7"/></svg></span><div><small>Email</small>info@snackorbit.com</div></div>
    <span class="sep"></span>
    <div class="contact"><span class="ic"><svg width="18" height="18" viewBox="0 0 24 24" fill="#fff"><path d="M12 2a7 7 0 0 0-7 7c0 5 7 13 7 13s7-8 7-13a7 7 0 0 0-7-7zm0 9.5a2.5 2.5 0 1 1 0-5 2.5 2.5 0 0 1 0 5z"/></svg></span><div>48, Cedar Ridge Plaza,<br>Pine Harbor, MI 49770</div></div>
    <span class="sep"></span>
    <div class="contact"><span class="ic"><svg width="18" height="18" viewBox="0 0 24 24" fill="none" stroke="#fff" stroke-width="1.6"><path d="M5 3h4l2 5-3 2a11 11 0 0 0 6 6l2-3 5 2v4a2 2 0 0 1-2 2A17 17 0 0 1 3 5a2 2 0 0 1 2-2z"/></svg></span><div><small>Phone</small><span class="big">231-555-0147</span></div></div>
  </div>
  <p class="legal">© 2024 SnackOrbit. All Rights Reserved.</p>
  <div class="socials"><span></span><span></span><span></span><span></span></div>
</footer>

</body>
</html>
```